Corvin Ridge Software PowerPoint template

We are a software company selling endpoint visibility, access and security technology to enterprise-level IT departments.
Our technology helps organizations gain comprehensive visibility into and control over devices accessing their corporate network so they can quickly identify and address suspicious activity on the network that could lead to potential threats like data breaches.
This technology can cost organizations upwards of $1M - depending on the size of the organization. Our primary clients are Vestral 2,000 companies.
We want a professional, polished PowerPoint template that we can use for all company presentations. Please include:
Title page
Section page
General info page
Thank you page
Logo options and color specs are attached.
Please include our tagline on at least the title page: Discover the edge. Optimize the whole.
Reason: Seeking more options. Looking for a clean design that uses lots of white space.
Software

```html
<!DOCTYPE html>
<html lang="en">
<head>
<meta charset="UTF-8">
<title>Corvin Ridge Software — Title Slide</title>
<link href="https://fonts.googleapis.com/css2?family=Exo+2:wght@300;400;600;700&display=swap" rel="stylesheet">
<style>
  :root {
    --brand-red: #8e1b22;
    --brand-copper: #c9825f;
    --text-grey: #777777;
    --rule-grey: #cfcfcf;
    --paper: #ffffff;
  }
  html, body {
    margin: 0;
    padding: 0;
    overflow: hidden;
    background: var(--paper);
  }
  .slide {
    position: relative;
    width: 1200px;
    height: 849px;
    background: var(--paper);
    overflow: hidden;
    font-family: "Exo 2", sans-serif;
  }
  .tagline {
    position: absolute;
    left: 138px;
    top: 128px;
    margin: 0;
    font-weight: 300;
    font-size: 66px;
    line-height: 74px;
    letter-spacing: -0.5px;
    color: var(--brand-red);
    text-transform: uppercase;
  }
  .presenter {
    position: absolute;
    left: 142px;
    top: 298px;
    margin: 0;
    font-weight: 600;
    font-size: 22px;
    color: var(--text-grey);
    text-transform: uppercase;
  }
  .date {
    position: absolute;
    left: 142px;
    top: 336px;
    margin: 0;
    font-weight: 400;
    font-size: 20px;
    color: var(--text-grey);
    text-transform: uppercase;
  }
  .brand-mark {
    position: absolute;
    left: 118px;
    top: 612px;
  }
  .brand-name {
    position: absolute;
    left: 268px;
    top: 636px;
    margin: 0;
    font-weight: 700;
    font-size: 44px;
    line-height: 52px;
    letter-spacing: 2px;
    color: var(--brand-red);
    text-transform: uppercase;
  }
  .footer-rule {
    position: absolute;
    left: 258px;
    top: 730px;
    width: 928px;
    height: 1px;
    background: var(--rule-grey);
  }
  .website {
    position: absolute;
    right: 70px;
    top: 742px;
    margin: 0;
    font-weight: 400;
    font-size: 16px;
    color: var(--text-grey);
    text-transform: uppercase;
  }
  .website strong { font-weight: 600; }
</style>
</head>
<body>
  <main class="slide">
    <h1 class="tagline">Discover the edge,<br>optimize the whole</h1>
    <p class="presenter">Name of the presentee</p>
    <p class="date">Date : MM DD YY</p>

    <svg class="brand-mark" width="120" height="120" viewBox="0 0 120 120" aria-hidden="true">
      <circle cx="60" cy="60" r="46" fill="var(--brand-copper)"/>
    </svg>
    <p class="brand-name">Corvin Ridge Software</p>

    <div class="footer-rule"></div>
    <p class="website">www. <strong>corvinridge</strong>software.com</p>
  </main>
</body>
</html>
```